Fernhollow Brochure - A new residential property investment development in Brisbane Queensland *

I need a brochure to entice and inspire customers of financial planners and alike to buy our investment property development, Fernhollow in Greenbank, Australia.

The brochure will be approximately 16 - 18 pages long and will follow a similar format (including maps etc) to the once attached in the uploaded files, however it is important that it has it's own unique style and brand identify. You will have access to all the renders, maps and autocad drawings that will need to be included in the brochure and will be linked in my dropbox link below.

The brochure should feel sophisticated and use the logo we've previously had developed on studio hive. The background and text should also match the style guidelines of our logo's although happy for you to to get creative with the background as long as it is relevant and fits with the colours. For example stock photo's of tree's, people playing, sunlight etc are great - although the context should be in Australia.

There will be a bit of back and forth once I select the winning designer to ensure the brochure is perfect. I'll also need individual files of the masterplan.

Look forward to seeing your designs.

https://www.filecrate-example.net/sh/q8wz3mfa1tp9rdx/KPLx7vnM2_TTqeZb4Hw9kY1uc?dl=0

Target Market(s)

Financial Planners and their consumer customers

Industry/Entity Type

Real Estate Development

Font styles to use
Other font styles liked:
• Monserrat - as per branding guidelines

Requirements
Must have
• At least all the elements that exist in the example brochures and outlined in the content

dropbox link - https://www.filecrate-example.net/sh/q8wz3mfa1tp9rdx/KPLx7vnM2_TTqeZb4Hw9kY1uc?dl=0

```html
<!DOCTYPE html>
<html lang="en">
<head>
<meta charset="utf-8">
<title>Fernhollow Brochure Spreads</title>
<link href="https://fonts.googleapis.com/css2?family=Libre+Caslon+Text&family=Montserrat:wght@400;500;600&display=swap" rel="stylesheet">
<style>
:root{
  --bg:#d6d6d6;
  --paper:#ffffff;
  --brand:#2f5d7c;
  --brand-deep:#285473;
  --ink:#2c5a84;
  --accent:#e0583a;
  --muted:#8c979f;
  --serif:"Libre Caslon Text", Georgia, serif;
  --sans:"Montserrat", Arial, sans-serif;
}
*{box-sizing:border-box;margin:0;padding:0}
html,body{width:884px;height:1200px;overflow:hidden;background:var(--bg)}
.canvas{position:relative;width:884px;height:1200px}
.pg{position:absolute;width:194px;height:150px;background:var(--paper);overflow:hidden;box-shadow:0 1px 3px rgba(0,0,0,.18)}
.photo{position:absolute}
.foot{position:absolute;left:0;right:0;bottom:0;height:13px;background:var(--paper);display:flex;align-items:center;justify-content:space-between;padding:0 9px}
.foot b{font-family:var(--serif);font-weight:400;font-size:3.2px;letter-spacing:.2px;color:var(--brand)}
.foot i{font-style:normal;font-family:var(--sans);font-size:2.4px;color:var(--muted)}
.h{position:absolute;font-family:var(--serif);color:var(--ink);text-transform:uppercase;font-size:6.6px;line-height:1.15;font-weight:400}
.t{position:absolute;font-family:var(--sans);font-size:2.3px;line-height:1.4;color:var(--muted)}
.t strong{display:block;color:var(--ink);font-weight:600}
.rule{position:absolute;height:.7px;width:9px;background:var(--accent)}
.stat-label{position:absolute;font-family:var(--sans);font-size:2.4px;color:#5b6670}
.stat{position:absolute;font-family:var(--serif);font-size:6.3px;color:var(--ink)}
.stat small{display:block;font-family:var(--sans);font-size:2px;color:var(--muted);line-height:1.3}
.wordmark{position:absolute;font-family:var(--serif);color:#fff;letter-spacing:.6px;text-transform:uppercase}
.logo-tile{position:absolute;width:24px;height:8px;border-radius:1.5px;background:#c9ced3}
</style>
</head>
<body>
<main class="canvas">

<!-- Cover -->
<section class="pg cover" style="left:44px;top:41px;background:var(--brand)">
  <div class="photo" role="img" aria-label="Father and son walking along a leafy suburban path" style="left:0;top:0;width:82px;height:150px;background:linear-gradient(160deg,#8aa56a,#4d6a3e 55%,#9b9a8a)"></div>
  <div class="wordmark" style="left:82px;width:112px;top:70px;text-align:center;font-size:9.5px">Fernhollow</div>
</section>

<!-- Spread: contents -->
<section class="pg" style="left:44px;top:202px">
  <div class="h" style="left:13px;top:34px;color:var(--accent);font-size:7px">Content</div>
  <div class="rule" style="left:13px;top:44px"></div>
  <div class="t" style="left:13px;top:50px;line-height:3.3">About<br>Location proximity<br>Sense of community<br>Investment<br>Points of interest<br>Masterplan<br>House plans<br>Package inclusions</div>
  <div class="photo" role="img" aria-label="Render of modern single-storey homes on a grassy street" style="left:72px;top:0;width:122px;height:137px;background:linear-gradient(180deg,#cfe0ec 0%,#e8eef2 40%,#9aa19b 62%,#6f8a4c 100%)"></div>
  <div class="foot"><b>Fernhollow</b><i>01</i></div>
</section>
<section class="pg" style="left:238px;top:202px">
  <div class="photo" role="img" aria-label="Render of modern homes continued across the spread" style="left:0;top:0;width:194px;height:137px;background:linear-gradient(180deg,#cfe0ec 0%,#e8eef2 40%,#8e918c 62%,#6f8a4c 100%)"></div>
  <div class="foot"><b>Fernhollow</b><i>02</i></div>
</section>

<!-- Spread: opportunity -->
<section class="pg" style="left:447px;top:202px">
  <div class="photo" role="img" aria-label="Smiling woman in a denim shirt" style="left:0;top:0;width:194px;height:137px;background:linear-gradient(120deg,#3a3430,#7a6757 55%,#4b5e78)"></div>
  <div class="foot"><b>Fernhollow</b><i>03</i></div>
</section>
<section class="pg" style="left:641px;top:202px">
  <div class="h" style="left:13px;top:15px;width:90px">An opportunity to invest in long term value creation</div>
  <div class="t" style="left:13px;top:62px;width:40px">Welcome to Fernhollow, a carefully crafted neighbourhood bringing people together. Every home is architecturally designed to create an inviting sense of place, with superior finishes and generous inclusions as standard.</div>
  <div class="t" style="left:58px;top:62px;width:40px">Nestled between Brisbane and the Gold Coast, Fernhollow sits close to key amenities, public transport and major roads. With a limited number of homes available, this is a rare wealth-creation opportunity.</div>
  <div class="photo" role="img" aria-label="Woman reading on a picnic rug among trees" style="left:107px;top:0;width:87px;height:137px;background:linear-gradient(170deg,#a9b98a,#6f8656 50%,#5e7196)"></div>
  <div class="foot"><b>Fernhollow</b><i>04</i></div>
</section>

<!-- Spread: lifestyle -->
<section class="pg" style="left:44px;top:362px">
  <div class="photo" role="img" aria-label="Woman shopping for fresh produce at a market" style="left:0;top:0;width:194px;height:137px;background:linear-gradient(110deg,#3c2a22,#7b5c3f 40%,#b8b9a6 65%,#8e9d68)"></div>
  <div class="foot"><b>Fernhollow</b><i>05</i></div>
</section>
<section class="pg" style="left:238px;top:362px">
  <div style="position:absolute;left:0;top:0;width:194px;height:31px;background:var(--brand)"></div>
  <div class="t" style="left:11px;top:11px;width:170px;color:#fff;font-size:2.6px">Fernhollow - escape the hustle and bustle with easy access to established and new amenities. Everything you need is close by, from the morning coffee to the express to work.</div>
  <div class="t" style="left:11px;top:40px;width:54px"><strong>Child care centres, nearby primary and secondary schools.</strong>Local state primary and high schools are a short drive, with private colleges and a university campus within easy reach.</div>
  <div class="photo" role="img" aria-label="Girl playing on a rope swing" style="left:78px;top:40px;width:42px;height:37px;background:linear-gradient(150deg,#c7b49a,#8a9a78)"></div>
  <div class="photo" role="img" aria-label="Person walking in a park" style="left:11px;top:75px;width:54px;height:26px;background:linear-gradient(150deg,#2d3a2c,#6c7c58)"></div>
  <div class="t" style="left:11px;top:106px;width:54px"><strong>Transport.</strong>Park and ride is minutes away with buses to the city. The Gold Coast is under an hour.</div>
  <div style="position:absolute;left:126px;top:40px;width:.5px;height:86px;background:var(--accent)"></div>
  <div class="t" style="left:130px;top:40px;width:50px"><strong>Local parks &amp; sporting facilities.</strong>A bushland reserve offers a safe place for families, with sports fields, an aquatic centre and a golf club nearby.</div>
  <div class="t" style="left:80px;top:90px;width:42px;text-align:right"><strong>Medical clinics and specialist support services.</strong>Clinics are a short drive away, with more options in neighbouring suburbs.</div>
  <div class="photo" role="img" aria-label="Dried grasses in a vase" style="left:130px;top:87px;width:44px;height:38px;background:linear-gradient(150deg,#efe7dc,#c2ab87)"></div>
  <div class="foot"><b>Fernhollow</b><i>06</i></div>
</section>

<!-- Spread: location -->
<section class="pg" style="left:447px;top:362px">
  <div class="photo" role="img" aria-label="Street map of the surrounding suburbs with points of interest" style="left:0;top:0;width:194px;height:137px;background:linear-gradient(135deg,#eef0f0,#e3e8e2)"></div>
  <div class="foot"><b>Fernhollow</b><i>07</i></div>
</section>
<section class="pg" style="left:641px;top:362px">
  <svg style="position:absolute;left:18px;top:16px" width="14" height="10" viewBox="0 0 14 10" aria-hidden="true">
    <path d="M4 9 C1 5 1.5 1 4 1 C6.5 1 7 5 4 9Z" fill="none" stroke="#7f8a93" stroke-width=".5"/>
    <path d="M10 9 C7 5 7.5 2 10 2 C12.5 2 13 5 10 9Z" fill="none" stroke="#7f8a93" stroke-width=".5"/>
  </svg>
  <svg style="position:absolute;left:80px;top:17px" width="10" height="10" viewBox="0 0 10 10" aria-hidden="true">
    <circle cx="5" cy="5" r="4.3" fill="none" stroke="#7f8a93" stroke-width=".5"/>
    <path d="M5 2.4V5L6.8 6" fill="none" stroke="#7f8a93" stroke-width=".5"/>
  </svg>
  <div class="h" style="left:18px;top:34px;font-size:7px;text-transform:none">KM's</div>
  <div class="h" style="left:80px;top:34px;font-size:7px;text-transform:none">Time</div>
  <div class="rule" style="left:18px;top:44px;background:#dfe3e6"></div>
  <div class="rule" style="left:80px;top:44px;background:#dfe3e6"></div>
  <div class="stat" style="left:18px;top:50px"><small>Ridgeway Town Centre</small>2.5km</div>
  <div class="stat" style="left:18px;top:66px"><small>Plainsway Shopping Centre</small>7km</div>
  <div class="stat" style="left:18px;top:82px"><small>Ridgeview Private Hospital</small>17km</div>
  <div class="stat" style="left:18px;top:98px"><small>Lakeside Golf Course</small>20km</div>
  <div class="stat" style="left:80px;top:50px"><small>Logan City</small>20 minutes</div>
  <div class="stat" style="left:80px;top:66px"><small>Airport</small>35 minutes</div>
  <div class="stat" style="left:80px;top:82px"><small>Gold Coast</small>59 minutes</div>
  <div class="stat" style="left:80px;top:98px"><small>Brisbane City</small>30 minutes</div>
  <div class="photo" role="img" aria-label="Golden wildflowers backlit by late sun" style="left:134px;top:0;width:60px;height:137px;background:linear-gradient(160deg,#2c2416,#8b6a2f 50%,#d7b46a)"></div>
  <div class="foot"><b>Fernhollow</b><i>08</i></div>
</section>

<!-- Spread: aerial -->
<section class="pg" style="left:44px;top:525px">
  <div class="photo" role="img" aria-label="Aerial view of the site and surrounding acreage lots" style="left:0;top:0;width:194px;height:137px;background:linear-gradient(135deg,#4a5640,#6b7256 50%,#56604a)"></div>
  <div class="foot"><b>Fernhollow</b><i>09</i></div>
</section>
<section class="pg" style="left:238px;top:525px">
  <div class="photo" role="img" aria-label="Aerial view continued with the marked site at 42 Marlow Road" style="left:0;top:0;width:194px;height:137px;background:linear-gradient(135deg,#56604a,#707659 60%,#8a8a7a)"></div>
  <svg style="position:absolute;left:27px;top:42px" width="6" height="8" viewBox="0 0 6 8" aria-hidden="true"><path d="M3 8C.5 5 0 3.8 0 3a3 3 0 0 1 6 0c0 .8-.5 2-3 5Z" fill="#e0442e"/><circle cx="3" cy="3" r="1" fill="#fff"/></svg>
  <div class="t" style="left:34px;top:44px;color:#fff;font-size:2.6px">42 Marlow Road</div>
  <div class="foot"><b>Fernhollow</b><i>10</i></div>
</section>

<!-- Spread: growth -->
<section class="pg" style="left:447px;top:525px">
  <div class="h" style="left:10px;top:14px;width:108px">Greenbank's only exclusively curated development. Imagine the potential.</div>
  <div class="photo" role="img" aria-label="Native grasses glowing in sunlight" style="left:118px;top:0;width:76px;height:62px;background:linear-gradient(160deg,#3a2e1e,#9c7d4a 55%,#d2b27b)"></div>
  <div class="t" style="left:10px;top:55px;width:100px">With only 53 lots available, this is your chance to secure a unique investment opportunity next door to a booming city.</div>
  <div class="h" style="left:10px;top:70px;font-size:4.4px">One of Queensland's largest and fastest growing cities</div>
  <div class="photo" role="img" aria-label="Child playing outdoors in the sun" style="left:0;top:82px;width:62px;height:49px;background:linear-gradient(140deg,#d9c79b,#7d7a55 60%,#3f4b3a)"></div>
  <div class="stat-label" style="left:71px;top:82px">Secured infrastructure improvements</div>
  <div class="stat" style="left:71px;top:87px">$134 million<small>worth of infrastructure investment</small></div>
  <div class="stat" style="left:71px;top:103px">$1.2 billion<small style="width:60px">deal between state government, council and property developers over the next 40 years</small></div>
  <div class="stat-label" style="left:137px;top:82px">Proven investment yields</div>
  <div class="stat" style="left:137px;top:87px"><small>High rental population</small>47.78%</div>
  <div class="stat" style="left:137px;top:102px"><small>Low vacancy rate</small>2.17%</div>
  <div class="stat" style="left:137px;top:117px"><small>Overall rental yield</small>5.24%</div>
  <div class="foot"><b>Fernhollow</b><i>11</i></div>
</section>
<section class="pg" style="left:641px;top:525px">
  <div class="h" style="left:17px;top:14px;width:170px;font-size:6.4px">With strong economic growth, a population increase of 22.6% in 10 years and $1.34 billion in planned infrastructure projects, this is a region that's surging ahead.</div>
  <div class="stat-label" style="left:17px;top:68px">Employment Growth</div>
  <div class="stat" style="left:17px;top:74px">200%<small>growth rate</small><small style="width:46px;margin-top:2px">Jobs projected to double in the region between 2016 and 2041</small></div>
  <div class="stat-label" style="left:76px;top:68px">Population Growth</div>
  <div class="stat" style="left:76px;top:74px">3.6%<small>growth rate</small></div>
  <div class="stat" style="left:76px;top:88px"><small>increase of</small>4,330<small>per year</small></div>
  <div class="stat" style="left:76px;top:115px">50%<small>increase in the next 25 years</small></div>
  <div class="photo" role="img" aria-label="Young woman outdoors in warm light" style="left:121px;top:65px;width:73px;height:66px;background:linear-gradient(140deg,#e8d9b4,#9a8a62 55%,#4f5a3a)"></div>
  <div class="foot"><b>Fernhollow</b><i>12</i></div>
</section>

<!-- Spread: turn-key -->
<section class="pg" style="left:44px;top:687px">
  <div class="h" style="left:10px;top:14px;width:100px;font-size:6.4px">An astute, turn-key investment solution where everything is taken care of</div>
  <div class="rule" style="left:10px;top:51px"></div>
  <div class="photo" role="img" aria-label="Home facade render" style="left:10px;top:59px;width:44px;height:20px;background:linear-gradient(180deg,#d6e4ee,#9a9d98 60%,#6f8a4c)"></div>
  <div class="photo" role="img" aria-label="Home facade render" style="left:10px;top:83px;width:44px;height:20px;background:linear-gradient(180deg,#d6e4ee,#8f928e 60%,#6f8a4c)"></div>
  <div class="photo" role="img" aria-label="Home facade render" style="left:10px;top:107px;width:44px;height:20px;background:linear-gradient(180deg,#d6e4ee,#a3a49f 60%,#6f8a4c)"></div>
  <div class="t" style="left:60px;top:60px;width:48px">Fernhollow's fixed price home and land packages surpass the rest for style and value. Each architecturally designed home is crafted by a premier builder to balance natural and urban expression with curated, timeless appeal.</div>
  <div class="photo" role="img" aria-label="Close view of a modern home entry" style="left:122px;top:0;width:72px;height:137px;background:linear-gradient(180deg,#cfe0ec,#5d5d5a 45%,#6f8a4c)"></div>
  <div class="foot"><b>Fernhollow</b><i>13</i></div>
</section>
<section class="pg" style="left:238px;top:687px">
  <div class="h" style="left:13px;top:22px;width:50px">This is living</div>
  <div class="t" style="left:13px;top:47px;width:50px">Choose from 10 stylish and contemporary home designs, all appointed with a premium selection of fixtures, quality finishes and pendant lighting as standard. Designed to complement their natural surroundings, these homes are as livable as they are functional.</div>
  <div class="photo" role="img" aria-label="Bedroom interior render" style="left:4px;top:91px;width:60px;height:46px;background:linear-gradient(170deg,#ecebe6,#b7b1a5 60%,#6d7a5c)"></div>
  <div class="photo" role="img" aria-label="Living room interior render" style="left:68px;top:0;width:126px;height:137px;background:linear-gradient(170deg,#f2f1ee,#d8d5cf 55%,#8b8680)"></div>
  <div class="foot"><b>Fernhollow</b><i>14</i></div>
</section>

<!-- Spread: masterplan -->
<section class="pg" style="left:447px;top:687px">
  <div class="photo" role="img" aria-label="Colour-coded masterplan showing lots and house designs" style="left:5px;top:8px;width:184px;height:122px;background:linear-gradient(120deg,#c56b8e,#7a68b8 25%,#4f9bd1 45%,#7cc267 65%,#e9c74a 82%,#d7573f)"></div>
  <div class="foot"><b>Fernhollow</b><i>15</i></div>
</section>
<section class="pg" style="left:641px;top:687px">
  <div style="position:absolute;left:12px;top:9px;width:116px;display:grid;grid-template-columns:repeat(3,37px);column-gap:2.5px;row-gap:6px">
    <div><div role="img" aria-label="Aspen home render" style="height:21px;background:linear-gradient(180deg,#d6e4ee,#9a9d98 60%,#6f8a4c)"></div><div class="t" style="position:static">The Aspen</div></div>
    <div><div role="img" aria-label="Banksia home render" style="height:21px;background:linear-gradient(180deg,#d6e4ee,#8f928e 60%,#6f8a4c)"></div><div class="t" style="position:static">The Banksia</div></div>
    <div><div role="img" aria-label="Cedar home render" style="height:21px;background:linear-gradient(180deg,#d6e4ee,#a3a49f 60%,#6f8a4c)"></div><div class="t" style="position:static">The Cedar</div></div>
    <div><div role="img" aria-label="Dune home render" style="height:21px;background:linear-gradient(180deg,#d6e4ee,#8f928e 60%,#6f8a4c)"></div><div class="t" style="position:static">The Dune</div></div>
    <div><div role="img" aria-label="Elm home render" style="height:21px;background:linear-gradient(180deg,#d6e4ee,#9a9d98 60%,#6f8a4c)"></div><div class="t" style="position:static">The Elm</div></div>
    <div><div role="img" aria-label="Fig home render" style="height:21px;background:linear-gradient(180deg,#d6e4ee,#a3a49f 60%,#6f8a4c)"></div><div class="t" style="position:static">The Fig</div></div>
    <div><div role="img" aria-label="Grove home render" style="height:21px;background:linear-gradient(180deg,#d6e4ee,#a3a49f 60%,#6f8a4c)"></div><div class="t" style="position:static">The Grove</div></div>
    <div><div role="img" aria-label="Heath home render" style="height:21px;background:linear-gradient(180deg,#d6e4ee,#9a9d98 60%,#6f8a4c)"></div><div class="t" style="position:static">The Heath</div></div>
    <div><div role="img" aria-label="Iris home render" style="height:21px;background:linear-gradient(180deg,#d6e4ee,#8f928e 60%,#6f8a4c)"></div><div class="t" style="position:static">The Iris</div></div>
    <div><div role="img" aria-label="Juniper home render" style="height:21px;background:linear-gradient(180deg,#d6e4ee,#9a9d98 60%,#6f8a4c)"></div><div class="t" style="position:static">The Juniper</div></div>
    <div><div role="img" aria-label="Kestrel home render" style="height:21px;background:linear-gradient(180deg,#d6e4ee,#a3a49f 60%,#6f8a4c)"></div><div class="t" style="position:static">The Kestrel</div></div>
    <div><div role="img" aria-label="Linden home render" style="height:21px;background:linear-gradient(180deg,#d6e4ee,#8f928e 60%,#6f8a4c)"></div><div class="t" style="position:static">The Linden</div></div>
  </div>
  <div class="photo" role="img" aria-label="Home entry and driveway render" style="left:139px;top:0;width:55px;height:137px;background:linear-gradient(180deg,#cfe0ec,#e6e6e2 35%,#3f3f3d 60%,#6f8a4c)"></div>
  <div class="foot"><b>Fernhollow</b><i>16</i></div>
</section>

<!-- Spread: points of difference -->
<section class="pg" style="left:44px;top:851px">
  <div class="h" style="left:10px;top:14px;width:100px">The Fernhollow build points of difference</div>
  <div class="t" style="left:10px;top:48px;color:#3c4a55;font-weight:600">Package inclusion</div>
  <ul class="t" style="left:14px;top:54px;width:95px;color:var(--accent);line-height:1.45">
    <li><span style="color:var(--muted)">Bespoke facades</span></li>
    <li><span style="color:var(--muted)">2590mm ceiling height</span></li>
    <li><span style="color:var(--muted)">Stone benchtops in kitchen and bathrooms</span></li>
    <li><span style="color:var(--muted)">Rendered brick letterbox</span></li>
    <li><span style="color:var(--muted)">Black tapware in kitchen</span></li>
    <li><span style="color:var(--muted)">Full render to the entire house</span></li>
    <li><span style="color:var(--muted)">Full landscaping package including front garden</span></li>
    <li><span style="color:var(--muted)">Turfing to the front and rear</span></li>
    <li><span style="color:var(--muted)">Fencing to the entire home</span></li>
    <li><span style="color:var(--muted)">Feature entry door</span></li>
    <li><span style="color:var(--muted)">Full blinds package to the entire home</span></li>
    <li><span style="color:var(--muted)">Exclusive builder for the entire development</span></li>
  </ul>
  <div class="photo" role="img" aria-label="Home exterior render" style="left:0;top:101px;width:53px;height:36px;background:linear-gradient(180deg,#d6e4ee,#9a9d98 60%,#6f8a4c)"></div>
  <div class="photo" role="img" aria-label="Kitchen interior render" style="left:56px;top:101px;width:59px;height:36px;background:linear-gradient(170deg,#f0eee9,#c9c1b2)"></div>
  <div class="photo" role="img" aria-label="Open plan living and dining render" style="left:117px;top:0;width:77px;height:137px;background:linear-gradient(170deg,#3d3d3b,#c9c8c3 40%,#a8a59e)"></div>
  <div class="foot"><b>Fernhollow</b><i>17</i></div>
</section>
<section class="pg" style="left:238px;top:851px">
  <div class="photo" role="img" aria-label="Dining area opening to the backyard" style="left:0;top:0;width:124px;height:137px;background:linear-gradient(170deg,#2f2f2d,#a9b0a2 40%,#b2aea6)"></div>
  <div class="photo" role="img" aria-label="Bathroom interior render" style="left:125px;top:0;width:69px;height:49px;background:linear-gradient(170deg,#efeeea,#b9b3a8)"></div>
  <div class="photo" role="img" aria-label="Hallway interior render" style="left:125px;top:53px;width:69px;height:41px;background:linear-gradient(170deg,#e9e8e4,#a8a49c)"></div>
  <div class="photo" role="img" aria-label="Living room interior render" style="left:125px;top:97px;width:69px;height:40px;background:linear-gradient(170deg,#e0ded9,#8e8a84)"></div>
  <div class="foot"><b>Fernhollow</b><i>18</i></div>
</section>

<!-- Spread: partners -->
<section class="pg" style="left:447px;top:851px">
  <div class="h" style="left:10px;top:14px;width:150px">Working with some of Australia's leading brands</div>
  <div class="rule" style="left:10px;top:36px"></div>
  <div class="logo-tile" style="left:15px;top:50px"></div><div class="logo-tile" style="left:47px;top:50px"></div><div class="logo-tile" style="left:79px;top:50px"></div><div class="logo-tile" style="left:111px;top:50px"></div><div class="logo-tile" style="left:143px;top:50px"></div>
  <div class="logo-tile" style="left:15px;top:70px"></div><div class="logo-tile" style="left:47px;top:70px"></div><div class="logo-tile" style="left:79px;top:70px"></div><div class="logo-tile" style="left:111px;top:70px"></div><div class="logo-tile" style="left:143px;top:70px"></div>
  <div class="logo-tile" style="left:15px;top:90px"></div><div class="logo-tile" style="left:47px;top:90px"></div><div class="logo-tile" style="left:79px;top:90px"></div><div class="logo-tile" style="left:111px;top:90px"></div><div class="logo-tile" style="left:143px;top:90px"></div>
  <div class="logo-tile" style="left:15px;top:110px"></div><div class="logo-tile" style="left:47px;top:110px"></div><div class="logo-tile" style="left:79px;top:110px"></div><div class="logo-tile" style="left:111px;top:110px"></div>
  <div class="foot"><b>Fernhollow</b><i>19</i></div>
</section>
<section class="pg" style="left:641px;top:851px">
  <div class="photo" role="img" aria-label="Young girl standing by a park fence" style="left:0;top:0;width:194px;height:137px;background:linear-gradient(150deg,#2b3a2a,#6f7b52 55%,#a7a37a)"></div>
  <div class="foot"><b>Fernhollow</b><i>20</i></div>
</section>

<!-- Back cover -->
<section class="pg back" style="left:641px;top:1014px;background:linear-gradient(180deg,#3a5f80,var(--brand-deep))">
  <div class="wordmark" style="left:0;width:194px;top:41px;text-align:center;font-size:8px">Fernhollow</div>
  <div class="wordmark" style="left:0;width:194px;top:63px;text-align:center;font-size:5px;line-height:1.45;letter-spacing:.2px">To find out how to secure<br>your investment in Fernhollow,</div>
  <div class="wordmark" style="left:0;width:194px;top:86px;text-align:center;font-size:5px;letter-spacing:.2px">Contact us now.</div>
  <div style="position:absolute;left:0;width:194px;top:100px;text-align:center;font-family:var(--sans);font-weight:600;font-size:4.4px;color:#fff">1300 555 019</div>
  <div style="position:absolute;left:0;width:194px;top:110px;text-align:center;font-family:var(--sans);font-size:3px;color:#fff">sales@fernhollow.com.au</div>
  <div style="position:absolute;left:0;width:194px;top:118px;text-align:center;font-family:var(--sans);font-size:2.8px;line-height:1.4;color:#fff">42 Marlow Rd, Greenbank<br>QLD 4124</div>
</section>

</main>
</body>
</html>
```